Electric mountain bike tours nz

We are an Electric Mountain bike tour company in New Zealand. We will be offering bike rental and guided tours around the Nelson region in New Zealand. I want our website to represent both Mountain biking and New Zealand with the colours layout and features. We want tabs for the following:
-1 about us
-2 what we offer
-3 bookings/contact
Under the about us tab will be who we are as a a company. I want the ability to add videos to each of these tabs as we move foward with videos of the tracks we will be riding. I want the website to be editable so I can add and remove videos/photos myself. Also "our bikes" will be under this tab.
Under the what we offer tab will be
-1 bike rental and pricing
-2 guided tours and pricing
-3 recommended package deals.
I want to able to put the tracks under the guided tours tab and select beginner/ intermediate/advanced and have the tracks in each of the following to match the rider level. Also to be able to have a small video of the track would be great in this section.
Bookings and contact tab
(Further information for this tab to be updated soon)
Coded - Design and coding required
1 page
- Silver ferns, kiwi, mountains

```html
<!DOCTYPE html>
<html lang="en">
<head>
<meta charset="utf-8">
<title>Ridgevolt – Electric Mountain Bike Tours</title>
<link rel="stylesheet" href="https://fonts.googleapis.com/css2?family=Lato:wght@400;700;900&family=Open+Sans:wght@600;700;800&display=swap">
<style>
:root{
  --ink:#111111;
  --black:#0c0c0c;
  --white:#ffffff;
  --mist:#e8ebf2;
  --grey-text:#555555;
  --muted:#a8a8a8;
  --col-light:#f0f0f0;
  --col-mid:#dedede;
  --col-dark:#c2c2c2;
  --footer-bar:#3b3b3b;
  --footer-rule:#777777;
  --field-line:#8a8a8a;
  --submit:#b9b9b9;
}
*{box-sizing:border-box;margin:0;padding:0}
html,body{width:1200px;height:2769px;overflow:hidden}
body{position:relative;font-family:"Lato",sans-serif;color:var(--ink);background:var(--white)}
.abs{position:absolute}

/* hero */
.hero-photo{left:0;top:0;width:1200px;height:820px;
  background:linear-gradient(180deg,#c9d6e4 0%,#9aa8b4 18%,#6c7a6a 45%,#5f7440 70%,#7c8a3e 100%)}
.nav{left:0;top:55px;width:1200px;height:96px;background:var(--black)}
.brand{left:78px;top:78px;height:50px;display:flex;align-items:center;gap:10px;
  font-weight:900;font-size:26px;color:var(--white);letter-spacing:1px;white-space:nowrap}
.brand-dot{width:18px;height:18px;border-radius:50%;background:var(--white)}
.nav-links{left:540px;top:94px;display:flex;align-items:center;gap:22px;
  font-size:16px;color:var(--white);white-space:nowrap}
.nav-links svg{width:18px;height:26px}
.social{display:flex;gap:6px;margin-left:10px}
.social span{width:19px;height:19px;border-radius:50%;background:var(--white);display:block}
.hero-title{left:525px;top:340px;width:600px;text-align:center;font-family:"Open Sans",sans-serif;
  font-weight:700;font-size:56px;line-height:70px;color:var(--white)}
.hero-sub{left:610px;top:482px;width:430px;text-align:center;font-family:"Open Sans",sans-serif;
  font-weight:700;font-size:15px;line-height:22px;color:var(--white)}
.btn{display:flex;align-items:center;justify-content:center;
  font-weight:700;font-size:17px;letter-spacing:.3px;white-space:nowrap}
.btn-light{left:752px;top:580px;width:100px;height:30px;font-size:16px;background:var(--white);color:var(--ink)}
.btn-dark{background:var(--ink);color:var(--white)}

/* about */
.about{left:0;top:820px;width:1200px;height:441px;background:var(--mist)}
.video{left:87px;top:917px;width:397px;height:261px;
  background:linear-gradient(180deg,#c9d9ea 0%,#d5cdb8 55%,#a48a63 100%)}
.video-bar{left:87px;top:1141px;width:397px;height:37px;background:#1a1a1a}
.video-track{left:148px;top:1157px;width:318px;height:5px;background:#e6e6e6}
.video-progress{left:148px;top:1157px;width:120px;height:5px;background:#c8161d}
.play{left:263px;top:1030px;width:42px;height:42px;border-radius:50%;background:rgba(255,255,255,.85)}
.section-title{display:flex;align-items:center;gap:8px;font-weight:700;font-size:28px;white-space:nowrap}
.section-title .soft{color:var(--muted)}
.about-title{left:556px;top:870px}
.about-text{left:559px;top:930px;width:555px;font-size:14.6px;line-height:24px;color:var(--grey-text);text-align:justify}
.about-btn{left:557px;top:1200px;width:152px;height:30px}

/* bikes */
.bikes{left:0;top:1261px;width:1200px;height:469px;
  background:linear-gradient(120deg,#2f3a22 0%,#55623a 40%,#7a7046 70%,#3d3a2c 100%)}
.bikes-title{left:98px;top:1340px;color:var(--white)}
.bikes-title .soft{color:#cfcfcf}
.bikes-text{left:89px;top:1410px;width:375px;font-weight:700;font-size:15.5px;line-height:22.5px;color:var(--white)}
.bikes-btn{left:87px;top:1625px;width:149px;height:30px}

/* offer */
.offer-title{left:0;top:1750px;width:1200px;justify-content:center;font-size:28px}
.col{top:1870px;width:343px;height:447px}
.col-1{left:87px;background:var(--col-light)}
.col-2{left:430px;background:var(--col-mid)}
.col-3{left:773px;background:var(--col-dark)}
.col-head{top:1818px;font-weight:700;font-size:21.5px;color:var(--ink);white-space:nowrap}
.card{width:343px;height:116px}
.card-photo{position:absolute;left:0;top:0;width:116px;height:114px}
.card-body{position:absolute;left:135px;top:0;width:195px}
.card-body h3{font-size:15px;font-weight:700;margin-bottom:8px;margin-top:-2px}
.card-body p{font-size:12.3px;line-height:15px;color:var(--grey-text);text-align:justify}
.card-body .more{display:flex;align-items:center;gap:8px;margin-top:10px;font-size:11.5px;font-weight:700}
.photo-a{background:linear-gradient(160deg,#8fb3d6,#6f8a4e 60%,#4c5a2e)}
.photo-b{background:linear-gradient(160deg,#d9b56a,#7a6a3c 55%,#3a3526)}
.photo-c{background:linear-gradient(160deg,#a9c2dc,#7f9a5c 55%,#5c6b3a)}

/* footer */
.footer{left:0;top:2317px;width:1200px;height:397px;background:var(--black)}
.on-dark{color:var(--white)}
.footer-brand{left:114px;top:2372px;width:181px;height:176px;display:flex;align-items:center;justify-content:center;gap:8px;
  font-weight:900;font-size:26px;white-space:nowrap}
.follow{left:122px;top:2584px;width:200px;font-weight:700;font-size:15px;padding-bottom:8px;border-bottom:1px dotted var(--footer-rule)}
.footer-social{left:122px;top:2635px;display:flex;gap:6px}
.footer-social span{width:18px;height:18px;border-radius:50%;background:var(--white);display:block}
.f-head{font-family:"Open Sans",sans-serif;font-weight:600;font-size:19px;width:197px;padding-bottom:6px;border-bottom:1px dotted var(--footer-rule)}
.contact-head{left:377px;top:2373px}
.contact-lines{left:377px;top:2423px;font-size:11.5px;line-height:15px}
.contact-list{left:377px;top:2470px;font-size:11.5px;line-height:22.5px}
.contact-list div{display:flex;align-items:center;gap:6px}
.contact-list svg{width:10px;height:10px}
.quick-head{left:377px;top:2550px}
.quick-list{left:377px;top:2598px;font-size:11.5px;line-height:22.5px}
.quick-list div{display:flex;align-items:center;gap:14px}
.booking-head{left:650px;top:2375px;font-family:"Open Sans",sans-serif;font-weight:600;font-size:19px}
.field{border:1px solid var(--field-line);font-size:11.5px;padding:7px 6px;color:var(--white)}
.submit{left:650px;top:2631px;width:118px;height:27px;background:var(--submit);color:var(--white);
  font-size:13px;display:flex;align-items:center;justify-content:center}
.bottom-bar{left:0;top:2714px;width:1200px;height:55px;background:var(--footer-bar);color:#c8c8c8;
  font-size:14px;display:flex;align-items:center;justify-content:center;gap:8px}
</style>
</head>
<body>

<!-- Hero -->
<div class="abs hero-photo" role="img" aria-label="Two riders on electric mountain bikes on a grassy alpine trail below snowy mountains"></div>
<header class="abs nav"></header>
<div class="abs brand"><span class="brand-dot"></span>RIDGEVOLT</div>
<nav class="abs nav-links">
  <span>About us</span>
  <svg viewBox="0 0 18 26"><path d="M11 0 2 15h6l-3 11 11-16h-6l4-10z" fill="#fff"/></svg>
  <span>What we offer</span>
  <svg viewBox="0 0 18 26"><path d="M11 0 2 15h6l-3 11 11-16h-6l4-10z" fill="#fff"/></svg>
  <span>Bookings/Contact</span>
  <div class="social"><span></span><span></span><span></span><span></span><span></span></div>
</nav>
<h1 class="abs hero-title">LOREM IPSUM<br>DOLOR</h1>
<p class="abs hero-sub">We are an Electric Mountain bike tour company in New Zealand. We will be offering bike rental and guided tours around the Nelson region in New Zealand.</p>
<div class="abs btn btn-light">BOOK NOW</div>

<!-- About -->
<section class="abs about"></section>
<div class="abs video" role="img" aria-label="Video still of a rider on an electric mountain bike near wind turbines"></div>
<div class="abs play"></div>
<svg class="abs" style="left:277px;top:1041px" width="16" height="20" viewBox="0 0 16 20"><path d="M0 0 16 10 0 20z" fill="#222"/></svg>
<div class="abs video-bar"></div>
<svg class="abs" style="left:100px;top:1151px" width="34" height="16" viewBox="0 0 34 16"><path d="M0 0 10 8 0 16z" fill="#fff"/><rect x="20" y="0" width="4" height="16" fill="#fff"/><rect x="28" y="0" width="4" height="16" fill="#fff"/></svg>
<div class="abs video-track"></div>
<div class="abs video-progress"></div>
<h2 class="abs section-title about-title">
  <svg width="26" height="38" viewBox="0 0 18 26"><path d="M11 0 2 15h6l-3 11 11-16h-6l4-10z" fill="#9a9a9a"/></svg>
  <span>About <span class="soft">Us</span></span>
</h2>
<p class="abs about-text">Lorem ipsum dolor sit amet, consectetuer adipiscing elit. Aenean commodo ligula eget dolor. Aenean massa. Cum sociis natoque penatibus et magnis dis parturient montes, nascetur ridiculus mus. Donec quam felis, ultricies nec, pellentesque eu, pretium quis, sem. Nulla consequat massa quis enim. Donec pede justo, fringilla vel, aliquet nec, vulputate eget, arcu. In enim justo, rhoncus ut, imperdiet a, venenatis vitae, justo. Nullam dictum felis eu pede mollis pretium. Integer tincidunt. Cras dapibus. Vivamus elementum semper nisi.aliquet nec, vulputate eget, arcu. In enim justo, rhoncus ut, imperdiet a, venenatis vitae, justo. Nullam dictum felis eu pede mollis pretium. Integer tincidunt. Cras dapibus. Vivamus elementum semper nisi.n enim justo, rhoncus ut, imperdiet a</p>
<div class="abs btn btn-dark about-btn">BOOK NOW</div>

<!-- Our bikes -->
<section class="abs bikes" role="img" aria-label="Red electric mountain bike parked on a wooden bench in a sunlit alpine meadow"></section>
<h2 class="abs section-title bikes-title">
  <svg width="26" height="38" viewBox="0 0 18 26"><path d="M11 0 2 15h6l-3 11 11-16h-6l4-10z" fill="#d0d0d0"/></svg>
  <span>Our <span class="soft">Bikes</span></span>
</h2>
<p class="abs bikes-text">Lorem ipsum dolor sit amet, consectetuer adipiscing elit. Aenean commodo ligula eget dolor. Aenean massa. Cum sociis natoque penatibus et magnis dis parturient montes, nascetur ridiculus mus. Donec quam felis, ultricies nec, pellentesque eu, pretium quis, sem. Nulla consequat massa quis enim. Donec pede justo, fringilla vel, aliquet nec, vulputate eget, arcu.</p>
<div class="abs btn btn-dark bikes-btn">BOOK NOW</div>

<!-- What we offer -->
<h2 class="abs section-title offer-title"><span>What we <span class="soft">Offer</span></span></h2>
<h3 class="abs col-head" style="left:87px">Bike rental &amp; pricing</h3>
<h3 class="abs col-head" style="left:430px">Guided tours &amp; pricing</h3>
<h3 class="abs col-head" style="left:773px">Recommended package deals</h3>
<div class="abs col col-1"></div>
<div class="abs col col-2"></div>
<div class="abs col col-3"></div>

<!-- column 1 -->
<article class="abs card" style="left:87px;top:1874px"><div class="card-photo photo-a" role="img" aria-label="Rental bike on a coastal trail"></div><div class="card-body"><h3>Lorem ipsum dolor</h3><p>Lorem ipsum dolor sit amet, consectetuer adipiscing elit. Quid autem habent admirationis, cum prope accesseris?</p><div class="more">Read more <svg width="10" height="8" viewBox="0 0 10 8"><path d="M0 0 4 4 0 8M5 0 9 4 5 8" stroke="#111" fill="none" stroke-width="1.5"/></svg></div></div></article>
<article class="abs card" style="left:87px;top:2012px"><div class="card-photo photo-c" role="img" aria-label="Riders on a green valley track"></div><div class="card-body"><h3>Lorem ipsum dolor</h3><p>Lorem ipsum dolor sit amet, consectetuer adipiscing elit. Quid autem habent admirationis, cum prope accesseris?</p><div class="more">Read more <svg width="10" height="8" viewBox="0 0 10 8"><path d="M0 0 4 4 0 8M5 0 9 4 5 8" stroke="#111" fill="none" stroke-width="1.5"/></svg></div></div></article>
<article class="abs card" style="left:87px;top:2152px"><div class="card-photo photo-a" role="img" aria-label="Rider on a gravel path near wind turbines"></div><div class="card-body"><h3>Lorem ipsum dolor</h3><p>Lorem ipsum dolor sit amet, consectetuer adipiscing elit. Quid autem habent admirationis, cum prope accesseris?</p><div class="more">Read more <svg width="10" height="8" viewBox="0 0 10 8"><path d="M0 0 4 4 0 8M5 0 9 4 5 8" stroke="#111" fill="none" stroke-width="1.5"/></svg></div></div></article>

<!-- column 2 -->
<article class="abs card" style="left:430px;top:1874px"><div class="card-photo photo-b" role="img" aria-label="Beginner forest trail"></div><div class="card-body"><h3>Beginner</h3><p>Lorem ipsum dolor sit amet, consectetuer adipiscing elit. Quid autem habent admirationis, cum prope accesseris?</p><div class="more">Read more <svg width="10" height="8" viewBox="0 0 10 8"><path d="M0 0 4 4 0 8M5 0 9 4 5 8" stroke="#111" fill="none" stroke-width="1.5"/></svg></div></div></article>
<article class="abs card" style="left:430px;top:2012px"><div class="card-photo photo-b" role="img" aria-label="Intermediate group ride with bikes"></div><div class="card-body"><h3>Intermediate</h3><p>Lorem ipsum dolor sit amet, consectetuer adipiscing elit. Quid autem habent admirationis, cum prope accesseris?</p><div class="more">Read more <svg width="10" height="8" viewBox="0 0 10 8"><path d="M0 0 4 4 0 8M5 0 9 4 5 8" stroke="#111" fill="none" stroke-width="1.5"/></svg></div></div></article>
<article class="abs card" style="left:430px;top:2152px"><div class="card-photo photo-c" role="img" aria-label="Advanced downhill trail"></div><div class="card-body"><h3>Advanced</h3><p>Lorem ipsum dolor sit amet, consectetuer adipiscing elit. Quid autem habent admirationis, cum prope accesseris?</p><div class="more">Read more <svg width="10" height="8" viewBox="0 0 10 8"><path d="M0 0 4 4 0 8M5 0 9 4 5 8" stroke="#111" fill="none" stroke-width="1.5"/></svg></div></div></article>

<!-- column 3 -->
<article class="abs card" style="left:773px;top:1874px"><div class="card-photo photo-c" role="img" aria-label="Mountain valley package tour"></div><div class="card-body"><h3>Lorem ipsum dolor</h3><p>Lorem ipsum dolor sit amet, consectetuer adipiscing elit. Quid autem habent admirationis, cum prope accesseris?</p><div class="more">Read more <svg width="10" height="8" viewBox="0 0 10 8"><path d="M0 0 4 4 0 8M5 0 9 4 5 8" stroke="#111" fill="none" stroke-width="1.5"/></svg></div></div></article>
<article class="abs card" style="left:773px;top:2012px"><div class="card-photo photo-b" role="img" aria-label="Group of riders at sunset"></div><div class="card-body"><h3>Lorem ipsum dolor</h3><p>Lorem ipsum dolor sit amet, consectetuer adipiscing elit. Quid autem habent admirationis, cum prope accesseris?</p><div class="more">Read more <svg width="10" height="8" viewBox="0 0 10 8"><path d="M0 0 4 4 0 8M5 0 9 4 5 8" stroke="#111" fill="none" stroke-width="1.5"/></svg></div></div></article>
<article class="abs card" style="left:773px;top:2152px"><div class="card-photo photo-a" role="img" aria-label="Riders on a grassy hillside track"></div><div class="card-body"><h3>Lorem ipsum dolor</h3><p>Lorem ipsum dolor sit amet, consectetuer adipiscing elit. Quid autem habent admirationis, cum prope accesseris?</p><div class="more">Read more <svg width="10" height="8" viewBox="0 0 10 8"><path d="M0 0 4 4 0 8M5 0 9 4 5 8" stroke="#111" fill="none" stroke-width="1.5"/></svg></div></div></article>

<!-- Footer -->
<footer class="abs footer"></footer>
<div class="abs footer-brand on-dark"><span class="brand-dot"></span>RIDGEVOLT</div>
<div class="abs follow on-dark">FOLLOW US ON</div>
<div class="abs footer-social"><span></span><span></span><span></span><span></span><span></span></div>

<h4 class="abs f-head contact-head on-dark">Contact</h4>
<div class="abs contact-lines on-dark">42 Harbour Lane<br>Kestrel Bay 7010</div>
<div class="abs contact-list on-dark">
  <div><svg viewBox="0 0 10 10"><path d="M2 0h2l1 3-1.5 1a6 6 0 0 0 2.5 2.5L7 5l3 1v2a2 2 0 0 1-2 2A8 8 0 0 1 0 2a2 2 0 0 1 2-2z" fill="#fff"/></svg>555-014-2297</div>
  <div><svg viewBox="0 0 10 10"><rect x="0" y="2" width="10" height="7" fill="#fff"/><path d="M0 2 5 6 10 2" stroke="#000" fill="none"/></svg>hello@ridgevolt.example</div>
  <div><svg viewBox="0 0 10 10"><circle cx="5" cy="5" r="4.5" fill="none" stroke="#fff"/><path d="M0.5 5h9M5 .5c-2.5 3-2.5 6 0 9M5 .5c2.5 3 2.5 6 0 9" stroke="#fff" fill="none" stroke-width=".8"/></svg>www.ridgevolt.example</div>
</div>
<h4 class="abs f-head quick-head on-dark">QuickLinks</h4>
<div class="abs quick-list on-dark">
  <div><svg width="5" height="8" viewBox="0 0 5 8"><path d="M4 0 0 4 4 8" stroke="#fff" fill="none"/></svg>About us</div>
  <div><svg width="5" height="8" viewBox="0 0 5 8"><path d="M4 0 0 4 4 8" stroke="#fff" fill="none"/></svg>What we offer</div>
  <div><svg width="5" height="8" viewBox="0 0 5 8"><path d="M4 0 0 4 4 8" stroke="#fff" fill="none"/></svg>Bookings/Contact</div>
</div>

<h4 class="abs booking-head on-dark">Booking</h4>
<div class="abs field" style="left:650px;top:2424px;width:212px;height:33px">First Name:</div>
<div class="abs field" style="left:871px;top:2424px;width:214px;height:33px">LastName :</div>
<div class="abs field" style="left:650px;top:2468px;width:212px;height:33px">Phone No :</div>
<div class="abs field" style="left:871px;top:2468px;width:214px;height:33px">Email Address :</div>
<div class="abs field" style="left:650px;top:2512px;width:435px;height:85px">Message :</div>
<div class="abs submit">Submit</div>

<div class="abs bottom-bar"><span>© 2017 ridgevolt</span><span>|</span><span>Privacy Policy</span><span>|</span><span>User Agreement</span></div>

</body>
</html>
```